4th Generation Family Business Needs a New Card Design!

We are a family owned 4th Generation company. We are based in the Sydney, Australia area and we are desperately in need of a more modern and classy card. We are monumental masons who design, supply & erect lasting memorials throughout cemeteries in Sydney. Our customers are normally in a period of grieving. I have attached logo files that will need to be implemented on the card. Company was established 1935. Australian Owned and Operated. Card needs to be designed to PIXO.com specification.

Target Market(s)

Our target market is based upon people that a grieving for family members that have passed away. We also deal with alot of companies that own and operate cemeteries.

Industry/Entity Type

Business

Contact Information for Business Card

Simon Harcourt, Operations Manager, 0417293086, simon@harcourtmemorials.com.au
Lewis Harcourt, Director, 0491630572, lewis@harcourtmemorials.com.au
Phone # 02 9561 3048
Website: www.harcourtmemorials.com.au
Address: Suite 17, 8 Palfrey Lane, West Carlow, Sydney NSW 2156

Font styles to use
Serif
Decorative
Script

Requirements
Must have
• Would like to see the logo nicely implemented with a modern design. Embossed lettering would be a nice additive.

```html
<!DOCTYPE html>
<html lang="en">
<head>
<meta charset="utf-8">
<title>Harcourt Memorials – Business Card</title>
<link rel="stylesheet" href="https://fonts.googleapis.com/css2?family=Open+Sans:wght@400;600&display=swap">
<style>
  :root {
    --stage: #000000;
    --card-light: #f3f3f3;
    --card-gold: #e9bd2e;
    --gold: #e9b92a;
    --ink: #2a2a2a;
    --white: #ffffff;
  }
  * { margin: 0; padding: 0; box-sizing: border-box; }
  html, body { width: 1200px; height: 900px; overflow: hidden; background: var(--stage); }
  body { font-family: "Open Sans", Arial, sans-serif; position: relative; }

  .card { position: absolute; top: 200px; width: 310px; height: 502px; }
  .card--front { left: 265px; background: var(--card-light); border-radius: 60px 0 60px 0; }
  .card--back  { left: 641px; width: 309px; background: var(--card-gold); border-radius: 0 60px 0 60px; }

  .brand-name {
    position: absolute; left: 0; width: 100%;
    text-align: center; font-weight: 400; letter-spacing: 2px;
    line-height: 1.15; text-transform: uppercase;
  }
  .card--front .brand-name { top: 148px; left: -30px; font-size: 27px; color: var(--ink); }
  .card--back .brand-name { top: 172px; left: -10px; font-size: 27px; color: var(--white); }
  .brand-name .brand-line { display: block; }
  .brand-name .brand-line--small { font-size: 17px; letter-spacing: 4px; }

  .contacts { position: absolute; left: 25px; top: 280px; color: var(--ink); }
  .person { margin-bottom: 10px; }
  .person__name { color: var(--gold); font-weight: 600; font-size: 16px; line-height: 20px; }
  .person__role { font-size: 13px; line-height: 18px; margin-bottom: 6px; }
  .contact-line { display: flex; align-items: center; font-size: 13px; line-height: 18px; gap: 6px; }
  .contact-line svg { width: 10px; height: 10px; fill: var(--gold); flex: none; }

  .company-info { position: absolute; right: 37px; top: 342px; color: var(--white); text-align: right; }
  .info-line { display: flex; justify-content: flex-end; align-items: flex-start; gap: 10px; font-size: 13px; line-height: 18px; }
  .info-line svg { width: 11px; height: 11px; fill: var(--white); flex: none; margin-top: 4px; }
  .info-line--address { margin-top: 28px; }
  .info-line--address svg { height: 14px; }
</style>
</head>
<body>

<section class="card card--front">
  <div class="brand-name">
    <span class="brand-line">Harcourt</span>
    <span class="brand-line brand-line--small">Memorials</span>
  </div>

  <div class="contacts">
    <div class="person">
      <p class="person__name">Simon Harcourt</p>
      <p class="person__role">Operations Manager</p>
      <p class="contact-line"><svg viewBox="0 0 10 10"><path d="M2 0.5 L3.6 2.6 L2.7 3.6 Q3.8 6 6.4 7.3 L7.4 6.4 L9.5 8 L8.3 9.5 Q3.5 9 0.5 1.7 Z"/></svg>0417293086</p>
      <p class="contact-line"><svg viewBox="0 0 10 10"><path d="M0.5 2 H9.5 V8.5 H0.5 Z M1 2.5 L5 5.5 L9 2.5" stroke="#f3f3f3" stroke-width="0.8"/></svg>simon@harcourtmemorials.com.au</p>
    </div>
    <div class="person">
      <p class="person__name">Lewis Harcourt</p>
      <p class="person__role">Director</p>
      <p class="contact-line"><svg viewBox="0 0 10 10"><path d="M2 0.5 L3.6 2.6 L2.7 3.6 Q3.8 6 6.4 7.3 L7.4 6.4 L9.5 8 L8.3 9.5 Q3.5 9 0.5 1.7 Z"/></svg>0491630572</p>
      <p class="contact-line"><svg viewBox="0 0 10 10"><path d="M0.5 2 H9.5 V8.5 H0.5 Z M1 2.5 L5 5.5 L9 2.5" stroke="#f3f3f3" stroke-width="0.8"/></svg>lewis@harcourtmemorials.com.au</p>
    </div>
  </div>
</section>

<section class="card card--back">
  <div class="brand-name">
    <span class="brand-line">Harcourt</span>
    <span class="brand-line brand-line--small">Memorials</span>
  </div>

  <div class="company-info">
    <p class="info-line">02 9561 3048<svg viewBox="0 0 10 10"><path d="M2 0.5 L3.6 2.6 L2.7 3.6 Q3.8 6 6.4 7.3 L7.4 6.4 L9.5 8 L8.3 9.5 Q3.5 9 0.5 1.7 Z"/></svg></p>
    <p class="info-line">www.harcourtmemorials.com.au<svg viewBox="0 0 10 10"><circle cx="5" cy="5" r="5"/></svg></p>
    <p class="info-line info-line--address"><span>Suite 17, 8 Palfrey Lane, West Carlow,<br>Sydney NSW 2156</span><svg viewBox="0 0 10 14"><path d="M5 0 A5 5 0 0 1 10 5 C10 8 5 14 5 14 C5 14 0 8 0 5 A5 5 0 0 1 5 0 Z M5 3 A2 2 0 1 0 5 7 A2 2 0 1 0 5 3 Z" fill-rule="evenodd"/></svg></p>
  </div>
</section>

</body>
</html>
```